Accountability Project Graphics

I want to create 10 social media graphics (new Instagram size 4:5 (1080 x 1350 pixels) focusing on our Quilvo Accountability App, using any of the 3 pictures attached. Use the attached pics only, NO RANDOM STOCK PHOTOGRAPHY. For the color scheme, use the landing page colors/fonts (attached).
You can add any of the 3 photos attached but I mainly need BOLD text that includes these headlines and sub-headlines on them.
Please NOTE for all the headlines below, also add this sub-headline on each graphic:
Stay Consistent with RT in Your Pocket!
Here are the headlines:
• Stop Starting Over Every Monday
• You don't need more willpower. You need more support
• Built for women who are tired of doing this alone
• When Motivation Fades, RT Checks In
• The Support System You've Been Missing
• Support When Motivation Disappears
• What if RT Checked in Every Day?
• The Missing Piece Isn't Another Diet
• Eat the food you love. Stay accountable every day.
• One Bad Meal Doesn't Mean You Failed
women over 40 trying to lose weight

```html
<!DOCTYPE html>
<html lang="en">
<head>
<meta charset="UTF-8">
<title>Quilvo Accountability – Built for women</title>
<link href="https://fonts.googleapis.com/css2?family=Fraunces:opsz,wght@9..144,500;9..144,700;9..144,800&family=Nunito+Sans:wght@400;600;700&display=swap" rel="stylesheet">
<style>
  :root {
    --ink: #1b1034;
    --pink: #e2457c;
    --blush: #f8d9e2;
    --blush-light: #fbe9ee;
    --brush: #f2b3c7;
    --white: #ffffff;
    --denim-dark: #1f2c52;
    --denim: #3a4d7a;
  }
  * { margin: 0; padding: 0; box-sizing: border-box; }
  html, body { width: 900px; height: 1200px; overflow: hidden; }
  body { background: var(--blush); }
  .poster {
    position: relative;
    width: 900px;
    height: 1200px;
    overflow: hidden;
    background: linear-gradient(160deg, var(--blush-light) 0%, var(--blush) 55%, #f6cfdb 100%);
    font-family: "Fraunces", Georgia, serif;
    color: var(--ink);
  }
  .brush-circle {
    position: absolute;
    left: 470px; top: 105px;
    width: 470px; height: 470px;
    border-radius: 50%;
    background: radial-gradient(circle, rgba(242,179,199,0.75) 0%, rgba(242,179,199,0.55) 60%, rgba(242,179,199,0) 72%);
  }
  .photo {
    position: absolute;
    left: 414px; top: 226px;
    width: 486px; height: 974px;
    border-radius: 180px 180px 0 0;
    background: linear-gradient(90deg, var(--denim-dark) 0%, #f4f1f3 22%, #f4f1f3 45%, var(--denim) 62%, var(--denim-dark) 100%);
    opacity: 0.92;
  }
  .headline {
    position: absolute;
    left: 50px; top: 122px;
    font-weight: 800;
    font-size: 68px;
    line-height: 71px;
    letter-spacing: -1.5px;
    width: 355px;
  }
  .headline .accent { color: var(--pink); display: block; }
  .headline-underline { position: absolute; left: 46px; top: 586px; }
  .heart { position: absolute; }
  .heart-headline { left: 322px; top: 545px; }
  .tagline {
    position: absolute;
    left: 56px; top: 660px;
    font-weight: 500;
    font-size: 28px;
    line-height: 37px;
  }
  .tagline .accent { color: var(--pink); }
  .heart-tagline { left: 250px; top: 752px; }
  .call-badge { position: absolute; left: 53px; top: 856px; display: flex; align-items: center; }
  .call-icon {
    width: 81px; height: 77px;
    border-radius: 14px;
    background: var(--pink);
    display: flex; align-items: center; justify-content: center;
  }
  .call-divider { width: 2px; height: 78px; background: var(--pink); margin: 0 17px 0 18px; opacity: 0.8; }
  .call-text {
    font-family: "Nunito Sans", Arial, sans-serif;
    font-size: 20px;
    line-height: 25px;
    color: var(--ink);
  }
  .chat-pill {
    position: absolute;
    left: 55px; top: 972px;
    height: 41px;
    padding: 0 20px;
    border-radius: 21px;
    background: var(--white);
    display: flex; align-items: center;
    font-family: "Nunito Sans", Arial, sans-serif;
    font-weight: 700;
    font-size: 19px;
    z-index: 2;
    box-shadow: 0 2px 8px rgba(180,90,120,0.12);
  }
  .chat-pill .sender { color: var(--pink); margin-right: 5px; }
  .chat-bubble { position: absolute; left: 50px; top: 1004px; }
  .chat-message {
    position: absolute;
    left: 80px; top: 1038px;
    font-weight: 700;
    font-size: 33px;
    letter-spacing: -0.5px;
  }
  .chat-underline { position: absolute; left: 86px; top: 1088px; }
  .heart-chat { left: 350px; top: 1030px; }
  .sub-headline {
    position: absolute;
    left: 56px; top: 1150px;
    font-family: "Nunito Sans", Arial, sans-serif;
    font-weight: 700;
    font-size: 19px;
    color: var(--pink);
  }
</style>
</head>
<body>
  <main class="poster">
    <div class="brush-circle"></div>
    <div class="photo" role="img" aria-label="Two smiling women in denim, one in white trousers holding a microphone, arms around each other and laughing"></div>

    <h1 class="headline">Built for<br>women<br>who are<br>tired of<span class="accent">doing this<br>alone.</span></h1>
    <svg class="headline-underline" width="260" height="20" viewBox="0 0 260 20"><path d="M4 14 C80 6 180 4 256 8" stroke="var(--pink)" stroke-width="5" fill="none" stroke-linecap="round"/></svg>
    <svg class="heart heart-headline" width="62" height="80" viewBox="0 0 62 80"><path d="M20 76 C12 54 2 38 6 20 C9 8 22 6 28 20 C34 4 56 2 56 18 C56 36 36 54 20 76" stroke="var(--pink)" stroke-width="3" fill="none" stroke-linecap="round"/></svg>

    <p class="tagline">Real connection.<br>Real encouragement.<br><span class="accent">Always in<br>your pocket.</span></p>
    <svg class="heart heart-tagline" width="44" height="56" viewBox="0 0 62 80"><path d="M20 76 C12 54 2 38 6 20 C9 8 22 6 28 20 C34 4 56 2 56 18 C56 36 36 54 20 76" stroke="var(--pink)" stroke-width="3.5" fill="none" stroke-linecap="round"/></svg>

    <div class="call-badge">
      <div class="call-icon">
        <svg width="48" height="48" viewBox="0 0 48 48" fill="none" stroke="var(--white)" stroke-width="3.5" stroke-linecap="round" stroke-linejoin="round">
          <path d="M10 6 L17 6 L20 15 L15 19 C18 26 22 30 29 33 L33 28 L42 31 L42 38 C42 41 39 43 36 42 C20 38 10 28 6 12 C5 9 7 6 10 6 Z" fill="var(--white)"/>
          <path d="M28 14 C32 15 34 17 35 21"/>
          <path d="M29 7 C36 9 40 13 42 20"/>
        </svg>
      </div>
      <div class="call-divider"></div>
      <p class="call-text">Weekly<br>calls from RT</p>
    </div>

    <div class="chat-pill"><span class="sender">RT:</span> You good, sis?</div>
    <svg class="chat-bubble" width="382" height="134" viewBox="0 0 382 134">
      <path d="M18 2 H364 Q380 2 380 18 V106 Q380 122 364 122 H36 L2 132 L10 116 Q2 112 2 100 V18 Q2 2 18 2 Z" fill="rgba(255,255,255,0.82)" stroke="rgba(255,255,255,0.95)" stroke-width="2"/>
    </svg>
    <p class="chat-message">You’ve got this!</p>
    <svg class="chat-underline" width="256" height="16" viewBox="0 0 256 16"><path d="M3 12 C80 4 170 3 252 6" stroke="var(--pink)" stroke-width="4" fill="none" stroke-linecap="round"/></svg>
    <svg class="heart heart-chat" width="54" height="66" viewBox="0 0 62 80"><path d="M20 76 C12 54 2 38 6 20 C9 8 22 6 28 20 C34 4 56 2 56 18 C56 36 36 54 20 76" stroke="var(--pink)" stroke-width="3" fill="none" stroke-linecap="round"/></svg>

    <p class="sub-headline">Stay Consistent with RT in Your Pocket!</p>
  </main>
</body>
</html>
```